Captivating packaging design for sports company.

We need a packaging design that encompasses our resistance bands workout set. Our focus is quality, convenience, and versatility. The design should be tailored to our broad array of customer across all paths. We would like the packaging to reflect our brand and product features such as: the LBS(weight) listed on each of the bands, convenience for travel and at home, highest quality, for all fitness levels, and free eBook. We'd also like to include a couple of our reviews on the packaging. Please refer to our listing on Varlo for additional information https://www.shopvarlo.com/Brisklane-Athletics-Resistance-Workout-Carrying/dp/K47TR2XMNQ/ref=sr_1_1?ie=UTF8&qid=1470453588&sr=8-1&keywords=brisklane+athletics+resistance+bands
Please reach out with additional questions for any further details. Thank you.
Target Market(s)
Sports, fitness, and health enthusiasts of all ages.
Industry/Entity Type
It Company
Look and feel
Each slider illustrates characteristics of the customer's brand and the style your logo design should communicate.

```html
<!DOCTYPE html>
<html lang="en">
<head>
<meta charset="utf-8">
<title>Brisklane Athletics – Resistance Band Package Front</title>
<link rel="stylesheet" href="https://fonts.googleapis.com/css2?family=Montserrat:wght@700&family=Questrial&family=Lato:ital,wght@1,300&display=swap">
<style>
  :root {
    --stage: #ececec;
    --face-light: #e9e9e9;
    --face-mid: #d4d4d4;
    --ink: #1b1b1b;
    --panel: #2a2a2a;
    --black: #0d0d0d;
    --facet-1: #1a1a1a;
    --facet-2: #262626;
    --facet-3: #333333;
    --stripe: #bdbdbd;
    --white: #ffffff;
    --photo-top: #bdbdbd;
    --photo-bottom: #8e8e8e;
  }
  * { margin: 0; padding: 0; box-sizing: border-box; }
  html, body { width: 1200px; height: 900px; overflow: hidden; }
  body {
    background: radial-gradient(ellipse at 50% 40%, #f6f6f6 0%, var(--stage) 60%, #d9d9d9 100%);
    position: relative;
  }
  .package-front {
    position: absolute;
    left: 288px;
    top: 120px;
    width: 624px;
    height: 660px;
    background: linear-gradient(180deg, var(--face-light) 0%, var(--face-mid) 100%);
    overflow: hidden;
  }
  .package-art { position: absolute; inset: 0; }
  .brand {
    position: absolute;
    left: 38px;
    top: 62px;
    display: flex;
    align-items: center;
    gap: 12px;
  }
  .brand-dot {
    width: 46px;
    height: 46px;
    border-radius: 50%;
    background: var(--ink);
  }
  .brand-name {
    font-family: "Montserrat", sans-serif;
    font-weight: 700;
    color: var(--ink);
    font-size: 25px;
    line-height: 1.02;
    letter-spacing: 0.5px;
  }
  .brand-name span { display: block; }
  .title-block {
    position: absolute;
    left: 348px;
    top: 62px;
    color: var(--white);
  }
  .product-name {
    font-family: "Questrial", sans-serif;
    font-size: 33px;
    line-height: 1.08;
    font-weight: 400;
    padding-bottom: 8px;
    border-bottom: 1px solid rgba(255,255,255,0.35);
    width: 190px;
  }
  .product-detail {
    font-family: "Lato", sans-serif;
    font-style: italic;
    font-weight: 300;
    font-size: 18px;
    line-height: 1.62;
    margin-top: 8px;
    color: #dcdcdc;
  }
  .athlete-photo {
    position: absolute;
    left: 75px;
    top: 240px;
    width: 235px;
    height: 400px;
    background: linear-gradient(180deg, var(--photo-top) 0%, var(--photo-bottom) 100%);
    opacity: 0.55;
  }
</style>
</head>
<body>
  <main class="package-front">
    <svg class="package-art" width="624" height="660" viewBox="0 0 624 660" aria-hidden="true">
      <rect class="edge-strip" x="0" y="0" width="8" height="660" fill="var(--black)"/>
      <polygon class="title-panel" points="330,40 558,40 330,398" fill="var(--panel)"/>
      <polygon class="light-stripe" points="606,0 624,0 624,14 282,660 252,660" fill="var(--stripe)"/>
      <polygon class="dark-field" points="624,14 624,660 282,660" fill="var(--black)"/>
      <polygon class="facet" points="624,120 624,420 470,420" fill="var(--facet-2)"/>
      <polygon class="facet" points="624,260 624,560 520,560" fill="var(--facet-3)" opacity="0.7"/>
      <polygon class="facet" points="470,420 624,420 560,660 400,660" fill="var(--facet-1)"/>
      <polygon class="facet" points="560,0 624,0 624,60" fill="var(--facet-1)"/>
    </svg>

    <div class="athlete-photo" role="img" aria-label="Photo of an athlete in a lunge pulling a resistance band anchored to the floor"></div>

    <div class="brand">
      <div class="brand-dot"></div>
      <div class="brand-name"><span>BRISKLANE</span><span>ATHLETICS</span></div>
    </div>

    <div class="title-block">
      <h1 class="product-name">Resistance<br>Band</h1>
      <p class="product-detail">Workout Set<br>with<br>Door<br>Anchor</p>
    </div>
  </main>
</body>
</html>
```